Brightmill Data Works

Our company is about IT hardwares and IT solutions. IT hardware such as PC, RAMS, storage and servers. IT solutions such as project management, BA. We are also selling new technology too.

Target Market(s)

Consumer, Small to Medium Business, Corporate

Requirements
Must have
• The business card must have the following:
• Name:
• Title:
• Contact Number:
• Email address:
• Website:
• Color: Must match the logo color upgrade

```html
<!DOCTYPE html>
<html lang="en">
<head>
<meta charset="utf-8">
<title>Brightmill Data Works – Business Card</title>
<link rel="stylesheet" href="https://fonts.googleapis.com/css2?family=Saira+Semi+Condensed:wght@500;600&family=Roboto:wght@400&display=swap">
<style>
  :root {
    --page-bg: #e2e2e2;
    --card-front: #f4f4f4;
    --card-back: #424242;
    --pattern-tone: #4a4540;
    --ink: #3f3f3f;
    --copper: #d08a2e;
    --rule: #9a9a9a;
  }
  * { margin: 0; padding: 0; box-sizing: border-box; }
  html, body {
    width: 1200px;
    height: 960px;
    overflow: hidden;
    background: var(--page-bg);
  }
  .canvas {
    position: relative;
    width: 1200px;
    height: 960px;
  }
  .card {
    position: absolute;
    width: 601px;
    height: 343px;
  }
  .card--front {
    left: 314px;
    top: 113px;
    background: var(--card-front);
  }
  .card--back {
    left: 311px;
    top: 472px;
    background: var(--card-back);
  }
  .brand {
    position: absolute;
    right: 45px;
    top: 110px;
    text-align: right;
    font-family: "Saira Semi Condensed", sans-serif;
    font-weight: 600;
    font-size: 30px;
    line-height: 30px;
    letter-spacing: 1px;
    color: var(--ink);
    text-transform: uppercase;
  }
  .brand__mark {
    position: absolute;
    right: 88px;
    top: 50px;
    width: 34px;
    height: 34px;
    background: var(--copper);
  }
  .holder {
    position: absolute;
    left: 43px;
    top: 198px;
  }
  .holder__name {
    font-family: "Saira Semi Condensed", sans-serif;
    font-weight: 600;
    font-size: 28px;
    line-height: 30px;
    color: var(--ink);
    text-transform: uppercase;
  }
  .holder__title {
    font-family: "Saira Semi Condensed", sans-serif;
    font-weight: 500;
    font-size: 16px;
    line-height: 18px;
    color: var(--copper);
    text-transform: uppercase;
  }
  .divider {
    position: absolute;
    left: 43px;
    top: 257px;
    width: 514px;
    height: 1px;
    background: var(--rule);
  }
  .contact {
    position: absolute;
    left: 44px;
    top: 270px;
    font-family: "Roboto", sans-serif;
    font-size: 14px;
    line-height: 20px;
    color: var(--ink);
  }
  .website {
    position: absolute;
    right: 42px;
    top: 290px;
    font-family: "Roboto", sans-serif;
    font-size: 14px;
    line-height: 20px;
    color: var(--ink);
  }
  .back-pattern {
    position: absolute;
    inset: 0;
    background: linear-gradient(135deg, var(--pattern-tone), var(--card-back));
  }
  .back-brand {
    position: absolute;
    left: 0;
    right: 0;
    top: 150px;
    text-align: center;
    font-family: "Saira Semi Condensed", sans-serif;
    font-weight: 600;
    font-size: 30px;
    line-height: 36px;
    letter-spacing: 1px;
    color: var(--copper);
    text-transform: uppercase;
  }
</style>
</head>
<body>
<main class="canvas">
  <section class="card card--front" aria-label="Business card front">
    <div class="brand__mark"></div>
    <div class="brand">Brightmill Data Works</div>
    <div class="holder">
      <div class="holder__name">Daniel Hart</div>
      <div class="holder__title">CEO/Founder</div>
    </div>
    <div class="divider"></div>
    <div class="contact">
      <div>555 214 0387</div>
      <div>daniel@brightmilldata.com</div>
    </div>
    <div class="website">www.brightmilldata.com</div>
  </section>

  <section class="card card--back" aria-label="Business card back">
    <div class="back-pattern" role="img" aria-label="Repeating brand pattern in muted bronze tones"></div>
    <div class="back-brand">Brightmill Data Works</div>
  </section>
</main>
</body>
</html>
```